Puffy Clouds Cotton Candy

Looking for a logo design and business cards to help a 13 year old entrepreneur promote her cotton candy business.
Contact Information for Business Card
Name, Phone & Email
Colors
E54698
E96AAD
F1A4CE
F9D9EA
FCEFF6
A7469A
B969AE
D3A5CF
EDDBEB
F8F0F9
6B429C
8869AF
B7A5CE
E3DAEB
F3F0F8
Requirements
Must have
- A fun feel that is appropriate for a teenage girl selling cotton candy

```html
<!DOCTYPE html>
<html lang="en">
<head>
<meta charset="utf-8">
<title>Puffy Clouds Cotton Candy – Business Card</title>
<link rel="stylesheet" href="https://fonts.googleapis.com/css2?family=Questrial&family=Arimo:wght@400&display=swap">
<style>
  :root {
    --bg: #2a2a2c;
    --card: #1b1c1e;
    --card-back: #141416;
    --pink: #e54698;
    --purple: #6b429c;
    --purple-light: #8869af;
    --white: #f3f0f8;
    --rule: #d8d8d8;
  }
  * { margin: 0; padding: 0; box-sizing: border-box; }
  html, body {
    width: 1200px;
    height: 1108px;
    overflow: hidden;
    background: var(--bg);
  }
  .stage {
    position: relative;
    width: 1200px;
    height: 1108px;
  }
  .card {
    position: absolute;
    top: 204px;
    width: 420px;
    height: 700px;
    border-radius: 22px;
    overflow: hidden;
  }
  .card--front {
    left: 150px;
    background: var(--card);
    text-align: center;
    font-family: "Questrial", sans-serif;
  }
  .card--back {
    left: 630px;
    background: var(--card-back);
  }
  .brand-mark {
    display: block;
    margin: 78px auto 0;
    width: 150px;
    height: 150px;
  }
  .brand-name {
    margin-top: 26px;
    color: var(--pink);
    font-size: 50px;
    line-height: 1.05;
    letter-spacing: -0.5px;
  }
  .brand-name .line-2 {
    display: block;
    font-size: 36px;
    margin-top: 4px;
  }
  .person {
    margin-top: 96px;
  }
  .person-name {
    color: var(--pink);
    font-size: 32px;
    letter-spacing: 0.3px;
  }
  .person-role {
    color: var(--purple-light);
    font-size: 21px;
    margin-top: 2px;
  }
  .rule {
    width: 170px;
    height: 1px;
    margin: 22px auto 18px;
    background: var(--rule);
  }
  .contact {
    font-family: "Arimo", sans-serif;
    color: var(--white);
    font-size: 21px;
    line-height: 1.45;
    list-style: none;
  }
  .back-pattern {
    position: absolute;
    inset: 0;
    background:
      radial-gradient(circle at 85% 15%, #4a4a4e 0%, #2a2a2d 35%, #141416 70%);
  }
  .back-brand {
    position: absolute;
    left: 0;
    right: 0;
    top: 470px;
    display: flex;
    align-items: center;
    justify-content: center;
    gap: 10px;
    font-family: "Questrial", sans-serif;
    color: var(--pink);
    font-size: 20px;
  }
  .back-brand svg { width: 22px; height: 22px; }
</style>
</head>
<body>
<main class="stage">
  <section class="card card--front">
    <svg class="brand-mark" viewBox="0 0 150 150" aria-hidden="true">
      <circle cx="75" cy="75" r="70" fill="none" stroke="var(--pink)" stroke-width="6"/>
    </svg>
    <h1 class="brand-name">Puffy Clouds<span class="line-2">Cotton Candy</span></h1>
    <div class="person">
      <p class="person-name">Daniel Harper</p>
      <p class="person-role">Managing Director</p>
    </div>
    <div class="rule"></div>
    <ul class="contact">
      <li>044-987 654 321</li>
      <li>hello@puffyclouds.com</li>
    </ul>
  </section>

  <section class="card card--back">
    <div class="back-pattern" role="img" aria-label="Repeating glossy black embossed cotton candy pattern"></div>
    <p class="back-brand">
      <svg viewBox="0 0 22 22" aria-hidden="true"><circle cx="11" cy="11" r="9" fill="none" stroke="var(--pink)" stroke-width="2"/></svg>
      Puffy Clouds
    </p>
  </section>
</main>
</body>
</html>
```